Capability Statement - Fabricataion company

FOr our Steel/ Plastic Fabrication business were looking for design of "Capability Statement"
This document is like our business card so it has to be designed to highest level .
Content is attached . Unfortunately I dont have logo with High Resolution.
Would like the designer to produce better quality logo we currently have

```html
<!DOCTYPE html>
<html lang="en">
<head>
<meta charset="utf-8">
<title>Ironvale Capability Statement – Pages 7 to 12</title>
<link href="https://fonts.googleapis.com/css2?family=PT+Sans+Narrow:wght@400;700&family=PT+Sans:wght@700&family=Roboto:wght@300&display=swap" rel="stylesheet">
<style>
  :root{
    --blue:#1b94d3;
    --blue-dark:#1a7fc0;
    --grey:#8a8b8f;
    --grey-light:#e3e4e6;
    --text:#3b3b3d;
    --frame:#9fd2ee;
    --paper:#ffffff;
  }
  *{box-sizing:border-box;margin:0;padding:0}
  html,body{width:1200px;height:1200px;overflow:hidden;background:var(--paper)}
  .spread{position:relative;width:1200px;height:1200px}
  .page{
    position:absolute;width:359px;height:508px;background:var(--paper);
    border:1px solid var(--frame);overflow:hidden;
  }
  .brand{position:absolute;left:22px;top:22px}
  .brand-name{font:700 26px/1 "PT Sans",sans-serif;color:var(--blue);letter-spacing:.5px}
  .brand-tag{font:300 11px/1 "Roboto",sans-serif;color:var(--grey);margin-top:6px}
  .header-rule{position:absolute;left:0;top:69px;width:100%;height:4px;
    background:linear-gradient(90deg,#b9babd,#e9eaeb 80%,transparent)}
  .section-title{position:absolute;left:22px;top:86px;width:316px;height:19px;
    background:var(--blue);border-left:6px solid var(--grey);
    font:700 14.5px/19px "PT Sans Narrow",sans-serif;color:#fff;padding-left:7px}
  .body{position:absolute;left:22px;top:113px;width:316px;
    font:400 7.4px/10.3px "PT Sans Narrow",sans-serif;color:var(--text)}
  .body p{margin-bottom:3.5px}
  .callout{font:700 12px/14.5px "PT Sans Narrow",sans-serif;color:var(--blue-dark);
    margin:6px 0 0 12px}
  .divider{position:absolute;left:0;width:100%;height:6px;background:var(--grey)}
  .visual{position:absolute;left:0;width:100%;bottom:0}
  .footer-bar{position:absolute;left:22px;bottom:0;width:316px;height:12px;background:var(--grey)}
  .page-no{position:absolute;right:21px;bottom:12px;width:32px;height:11px;
    background:var(--blue);clip-path:polygon(28% 0,100% 0,100% 100%,0 100%);
    font:700 7.5px/11px "PT Sans",sans-serif;color:#fff;text-align:right;padding-right:5px}
</style>
</head>
<body>
<main class="spread">

  <section class="page" style="left:13px;top:65px">
    <div class="brand"><div class="brand-name">IRONVALE</div><div class="brand-tag">Design / Engineering / Fabrication</div></div>
    <div class="header-rule"></div>
    <h2 class="section-title">Industrial Storage and Process Tanks</h2>
    <div class="body">
      <p>Ironvale plastic tanks manufactured out of HDPE sheet, Polypropylene (PP) sheet, Polyvinylchloride (PVC) or other plastics provide long term, corrosion free environment ideal for a diverse range of applications. This incorporates bulk holding purposes to store potable water, chemical, waste and effluent applications. With tanks manufactured from high density polyethylene (HDPE) with carbon black in the resin, which is a UV stabiliser allows HDPE tanks to be used in an exposed environment and/ or in a buried application. With custom fabrication we can supply and fit a wide range of various components such as inlet &amp; outlet, flanges, threaded fittings, valves &amp; taps, inspection ports, level indicators, sight glasses, anchor points, and baffles.</p>
      <p class="callout">All our tanks are custom designed, fully fabricated to the highest standards offering up to 25 Years Design Life.</p>
    </div>
    <div class="divider" style="top:278px"></div>
    <div class="visual" role="img" aria-label="3D renderings of custom plastic process tanks and a bunded storage tank" style="top:284px;background:linear-gradient(135deg,#f4f5f7,#c9cbd0 60%,#e6e7ea)"></div>
    <div class="footer-bar"></div><div class="page-no">7</div>
  </section>

  <section class="page" style="left:419px;top:65px">
    <div class="brand"><div class="brand-name">IRONVALE</div><div class="brand-tag">Design / Engineering / Fabrication</div></div>
    <div class="header-rule"></div>
    <h2 class="section-title">CNC Capabilities</h2>
    <div class="body">
      <p>Our Australian manufactured CoreCut CNC router with 4m x 2 m bed has had a profound impact on the shop operations. The CNC has proven to be an efficient tool for producing complex, accurate and repeatable parts that simply cannot be matched with more traditional machinery. When parts get to assembly, they simply fit with little to no need for tweaking and adjustments.</p>
      <p>The CNC offers us a unique opportunity to benefit from a production quality piece of equipment in a custom shop environment. Ironvale also welcomes opportunities to use the CNC for production of component parts for commercial customers.</p>
      <p>Whether you are looking for custom one-of-a-kind project or need help producing large quantities of component parts, Ironvale has the capabilities to assist you with your project.</p>
    </div>
    <div class="divider" style="top:236px"></div>
    <div class="visual" role="img" aria-label="Photo of a large black CNC router with control cabinet" style="top:242px;background:radial-gradient(ellipse at 50% 50%,#4a4a4e 0%,#1c1c1e 30%,#ffffff 62%)"></div>
    <div class="footer-bar"></div><div class="page-no">8</div>
  </section>

  <section class="page" style="left:826px;top:65px">
    <div class="brand"><div class="brand-name">IRONVALE</div><div class="brand-tag">Design / Engineering / Fabrication</div></div>
    <div class="header-rule"></div>
    <h2 class="section-title">Chemical Bunds</h2>
    <div class="body">
      <p>It is an HSE requirement for tanks storing dangerous or hazardous chemicals to have a bund.</p>
      <p>Ironvale have a range of plastic bunded chemical storage tanks, bunds and drip trays which can help meet this legal requirement. Chemical bunds have an enviable record of limiting and preventing hazardous substances and chemical spills.</p>
      <p>Manufactured from sheet plastic, rigid or flexible, predominantly HDPE, our bunds have many advantages over other types such as speed of manufacturing, ease of installation, site specific design, and relocatable if required. Whatever your requirement is our Ironvale team can design and fabricate it to reduce your environmental and contamination risk.</p>
      <p>Chemical Bunds can be open top for indoor applications or enclosed for outdoor to stop rainwater from entering the bund and also used within buildings for process vessels.</p>
    </div>
    <div class="divider" style="top:250px"></div>
    <div class="visual" role="img" aria-label="Abstract photo of dark ink clouds swirling in magenta liquid" style="top:256px;background:radial-gradient(ellipse at 40% 40%,#4a1030,#c8195e 45%,#e8206a)"></div>
    <div class="footer-bar"></div><div class="page-no">9</div>
  </section>

  <section class="page" style="left:13px;top:623px">
    <div class="brand"><div class="brand-name">IRONVALE</div><div class="brand-tag">Design / Engineering / Fabrication</div></div>
    <div class="header-rule"></div>
    <h2 class="section-title">Lining/ Flow Promotion</h2>
    <div class="body">
      <p>Ironvale team can design, machine and install a variety of liners to chutes, launders, tanks and process equipment. Typically chutes are lined in UHMWPE to improve wear resistance and promote flow. Sheets are secured using cap bolts or welded studs. CNC machining of the liner ensures accurate placement of holes as well as a good mechanical fit for the fastener cap. We recommend that seams between sheets are welded to avoid material hang up.</p>
      <p>Other linings can be made in any thermoplastic, dependant on service requirements and such plastics include PVC, PE, PP, PVDF, ECTFE and PFA.</p>
    </div>
    <div class="divider" style="top:250px"></div>
    <div class="visual" role="img" aria-label="Photo of the inside of a chute lined with bolted white UHMWPE sheets" style="top:256px;background:linear-gradient(160deg,#d9d9d7,#bdbdba 55%,#cfcfcc)"></div>
    <div class="footer-bar"></div><div class="page-no">10</div>
  </section>

  <section class="page" style="left:419px;top:623px">
    <div class="brand"><div class="brand-name">IRONVALE</div><div class="brand-tag">Design / Engineering / Fabrication</div></div>
    <div class="header-rule"></div>
    <h2 class="section-title">Onsite Services</h2>
    <div class="body">
      <p>We offer a wide range of on-site services such as: Electrofusion, butt fusion, extrusion welding as well as solvent cement joining according to clients’ requirements.</p>
    </div>
    <div class="divider" style="top:158px"></div>
    <div class="visual" role="img" aria-label="Photos of large black HDPE pipes clamped in blue butt fusion welding machines" style="top:164px;background:linear-gradient(180deg,#2a2b2e,#5a5d63 45%,#2f5fae 65%,#1e1f22)"></div>
    <div class="footer-bar"></div><div class="page-no">11</div>
  </section>

  <section class="page" style="left:826px;top:623px">
    <div class="brand"><div class="brand-name">IRONVALE</div><div class="brand-tag">Design / Engineering / Fabrication</div></div>
    <div class="header-rule"></div>
    <h2 class="section-title">Steel Pipe Fabrication</h2>
    <div class="body">
      <p>Ironvale steel division manufactures in house a vast array of steel pipe components for our own pipeline applications or for external sale. From butt weld or flanged pipe fittings in equal and reduced tee’s, reducers, bends, all components are made and tested to your specifications and can include final coatings such as paint, hot dip galvanising, epoxy, or powder coating. Typically we manufacture to AS4041 however if you nominate a different specification we will review these requirements and manufacture in accordance.</p>
    </div>
    <div class="divider" style="top:217px"></div>
    <div class="visual" role="img" aria-label="Photos of fabricated flanged steel pipe spools and a pipe manifold in a workshop" style="top:223px;background:linear-gradient(170deg,#8a9aa6,#4f4a52 40%,#3c8a5a 85%)"></div>
    <div class="footer-bar"></div><div class="page-no">12</div>
  </section>

</main>
</body>
</html>
```